Creative Fitness Studio Feature Wall

Two feature walls within functional fitness studio, they need to be on brand and have a WOW factor.
Designed to inspire and motivate people to live a fit and healthy lifestyle whilst working out and bringing life to the studio, as an uplifting and inviting environment.

Please see current walls and also visit website www.velto4.com.au for inspiration.
Updates

Target Market(s)

health and fitness, healthy lifestyle

Industry/Entity Type

Fitness

Font styles to use
Other font styles liked:
• gothic

Colors

Designer to choose colors to be used in the design.

Requirements
Must have
• inspiration from website www.velto4.com.au ........... brand consistency
Nice to have
• WOW factor......... walk into the gym and it draws your attention.
Should not have
• Overly muscly people (bodybuilders)

```html
<!DOCTYPE html>
<html lang="en">
<head>
<meta charset="utf-8">
<title>Velto4 Fitness – Feature Wall</title>
<link rel="stylesheet" href="https://fonts.googleapis.com/css2?family=Roboto+Condensed:wght@700;800&family=Roboto:wght@400&display=swap">
<style>
  :root {
    --brand-green: #78be43;
    --ink: #1b1b1b;
    --bg-light: #ffffff;
    --bg-shade: #ececec;
    --tile-yoga: #5b5e64;
    --tile-core: #4a5090;
    --tile-ride-top: #d59a45;
    --tile-ride-bottom: #2e3823;
    --tile-night: #26261f;
  }
  html, body {
    margin: 0;
    padding: 0;
    width: 1200px;
    height: 1200px;
    overflow: hidden;
  }
  .wall {
    position: relative;
    width: 1200px;
    height: 1200px;
    overflow: hidden;
    background: linear-gradient(120deg, var(--bg-shade) 0%, var(--bg-light) 45%, #f4f4f4 100%);
    font-family: "Roboto Condensed", "Arial Narrow", sans-serif;
    color: var(--ink);
  }
  .tile-grid {
    position: absolute;
    inset: 0;
    width: 1200px;
    height: 1200px;
  }
  .tile--green { fill: var(--brand-green); }
  .tile--yoga { fill: var(--tile-yoga); }
  .tile--core { fill: var(--tile-core); }
  .tile--ride { fill: url(#rideTone); }
  .tile--night { fill: var(--tile-night); }
  .tile--hero { fill: url(#heroTone); }

  .brand {
    position: absolute;
    left: 58px;
    top: 150px;
    margin: 0;
    font-family: "Roboto Condensed", "Arial Narrow", sans-serif;
    font-weight: 700;
    font-size: 48px;
    line-height: 1;
    color: var(--ink);
    white-space: nowrap;
  }

  .headline {
    position: absolute;
    left: 70px;
    top: 588px;
    width: 480px;
    margin: 0;
    text-align: center;
    line-height: 1;
  }
  .headline__kicker {
    display: block;
    font-weight: 700;
    font-size: 44px;
  }
  .headline__main {
    display: block;
    font-weight: 800;
    font-size: 96px;
    letter-spacing: -4px;
    margin-top: 4px;
  }
  .tagline {
    position: absolute;
    left: 112px;
    top: 1012px;
    margin: 0;
    font-family: "Roboto", Arial, sans-serif;
    font-weight: 400;
    font-size: 37px;
    color: var(--ink);
    white-space: nowrap;
  }
</style>
</head>
<body>
<main class="wall">
  <svg class="tile-grid" viewBox="0 0 1200 1200" xmlns="http://www.w3.org/2000/svg">
    <defs>
      <linearGradient id="heroTone" gradientUnits="userSpaceOnUse" x1="0" y1="0" x2="0" y2="1200">
        <stop offset="0" stop-color="#2a2421"/>
        <stop offset="0.22" stop-color="#6a4f43"/>
        <stop offset="0.36" stop-color="#e6e2df"/>
        <stop offset="0.6" stop-color="#f0ece8"/>
        <stop offset="0.72" stop-color="#c99a7c"/>
        <stop offset="0.88" stop-color="#b98c72"/>
        <stop offset="1" stop-color="#d6d3d1"/>
      </linearGradient>
      <linearGradient id="rideTone" x1="0" y1="0" x2="0" y2="1">
        <stop offset="0" stop-color="var(--tile-ride-top)"/>
        <stop offset="1" stop-color="var(--tile-ride-bottom)"/>
      </linearGradient>
    </defs>

    <g class="accent-tiles">
      <polygon class="tile--green" points="436,-140 583,7 436,154 289,7"/>
      <polygon class="tile--green" points="758,-140 905,7 758,154 611,7"/>
      <polygon class="tile--green" points="1080,-140 1227,7 1080,154 933,7"/>
      <polygon class="tile--green" points="597,987 744,1134 597,1281 450,1134"/>
      <polygon class="tile--green" points="1241,987 1388,1134 1241,1281 1094,1134"/>
    </g>

    <g class="activity-tiles">
      <polygon class="tile--yoga" role="img" aria-label="Photo: woman in a yoga backbend on a mat" points="597,21 744,168 597,315 450,168"/>
      <polygon class="tile--core" role="img" aria-label="Photo: man doing sit-ups on a gym floor" points="758,182 905,329 758,476 611,329"/>
      <polygon class="tile--ride" role="img" aria-label="Photo: mountain biker riding at sunset" points="597,665 744,812 597,959 450,812"/>
      <polygon class="tile--night" role="img" aria-label="Photo: athlete training outdoors in low light" points="758,826 905,973 758,1120 611,973"/>
    </g>

    <g class="hero-tiles" role="img" aria-label="Photo: smiling athletic woman in a white hoodie and sports top">
      <polygon class="tile--hero" points="919,21 1066,168 919,315 772,168"/>
      <polygon class="tile--hero" points="1241,21 1388,168 1241,315 1094,168"/>
      <polygon class="tile--hero" points="1080,182 1227,329 1080,476 933,329"/>
      <polygon class="tile--hero" points="919,343 1066,490 919,637 772,490"/>
      <polygon class="tile--hero" points="1241,343 1388,490 1241,637 1094,490"/>
      <polygon class="tile--hero" points="758,504 905,651 758,798 611,651"/>
      <polygon class="tile--hero" points="1080,504 1227,651 1080,798 933,651"/>
      <polygon class="tile--hero" points="919,665 1066,812 919,959 772,812"/>
      <polygon class="tile--hero" points="1241,665 1388,812 1241,959 1094,812"/>
      <polygon class="tile--hero" points="1080,826 1227,973 1080,1120 933,973"/>
      <polygon class="tile--hero" points="919,987 1066,1134 919,1281 772,1134"/>
    </g>
  </svg>

  <p class="brand">Velto4 Fitness</p>

  <h1 class="headline">
    <span class="headline__kicker">STAY ADDICTED</span>
    <span class="headline__main">TO FITNESS</span>
  </h1>

  <p class="tagline">YOUR TEXT HERE</p>
</main>
</body>
</html>
```